FinTech company looking to revamp and expand client-facing interface for our financial models

Pellworth Engines currently has a very simple website that allows clients to interact with our financial models. We are looking to completely redesign the current site and add several extra pages to provide extra functionality. We want the design to have a modern, slick feel, that will work on both a desktop or a tablet. It should be straightforward for clients to move between different pages at any time, and clear from the layout how to interact with the more advanced features. We have included screenshots of existing pages in the attached design brief, as well as sketches of the functionality required by the new pages, but can't provide a direct link to the current site.
Target Market(s)
Professional investors that will be paying to access the interface
Industry/Entity Type
Finance
Number of Pages Required
4 page
Colors
Designer to choose colors to be used in the design.
Look and feel
Each slider illustrates characteristics of the customer's brand and the style your logo design should communicate.

```html
<!DOCTYPE html>
<html lang="en">
<head>
<meta charset="utf-8">
<title>Pellworth Engines – Backtest</title>
<link rel="stylesheet" href="https://fonts.googleapis.com/css2?family=Roboto:wght@400;500;700&family=Roboto+Condensed:wght@400&family=Open+Sans:wght@400&display=swap">
<style>
:root{
  --navy:#0b3064;
  --ink:#111;
  --black:#1a1a1a;
  --frame:#e4e4e4;
  --white:#fff;
  --row-alt:#efefef;
  --line:#e2e2e2;
  --blue:#3a6cb0;
  --olive:#b8b934;
  --green:#4c9a2a;
  --side:#333;
}
*{box-sizing:border-box;margin:0;padding:0}
html,body{width:1200px;height:1122px;overflow:hidden}
body{background:var(--frame);font-family:"Roboto",sans-serif;color:var(--ink);position:relative}
.app{position:absolute;left:14px;top:14px;width:1172px;height:1094px;background:linear-gradient(#e6e6e6,#f9f9f9 40%,#fafafa)}
.topnav{position:absolute;left:0;top:0;width:1172px;height:55px;background:var(--white);display:flex;font-weight:700;font-size:13px}
.topnav .cell{height:55px;display:flex;align-items:center;justify-content:center;border-right:1px solid #ececec;gap:7px}
.brand{width:166px;font-size:17px;letter-spacing:.3px}
.w83{width:83px}.gap{width:125px}
.models{width:130px}.sens{width:163px}.port{width:148px}
.backtest{width:140px;background:var(--navy);color:var(--white);border-right:none}
.topnav svg{display:block}
.sidetab{position:absolute;left:0;top:295px;width:46px;height:231px;background:var(--side);border-radius:0 4px 4px 0;color:#fff}
.sidetab span{position:absolute;left:23px;top:115px;transform:translate(-50%,-50%) rotate(-90deg);white-space:nowrap;font-size:15px;font-weight:500;letter-spacing:.5px}
.sidetab .toggle{position:absolute;left:33px;top:100px}
.chartcard{position:absolute;left:83px;top:92px;width:1071px;height:392px;background:var(--white);box-shadow:0 2px 8px rgba(0,0,0,.12);border-radius:3px;overflow:hidden}
.cardhead{height:79px;background:#efefef;position:relative}
.tab{position:absolute;bottom:0;height:33px;background:var(--white);display:flex;align-items:center;justify-content:center;font-size:12px;font-weight:500;color:#555;border-radius:2px 2px 0 0}
.tab.chart{left:51px;width:143px;background:var(--navy);color:#fff;font-weight:700}
.tab.t1{left:199px;width:83px}.tab.t2{left:286px;width:84px}.tab.t3{left:374px;width:83px}
.tab.t4{left:461px;width:83px;height:42px;background:var(--black);color:#fff;font-weight:700;align-items:flex-start;padding-top:14px}
.plot{position:absolute;left:0;top:79px}
.export{position:absolute;top:533px;display:flex;align-items:center;gap:6px;color:var(--navy);font-weight:700;font-size:16px}
.panel{position:absolute;top:567px;height:453px;background:var(--white);box-shadow:0 2px 6px rgba(0,0,0,.15);border-radius:4px;overflow:hidden}
.stats{left:83px;width:369px}
.trades{left:489px;width:665px}
.panel table{border-collapse:collapse;table-layout:fixed}
.panel th{height:65px;background:var(--black);color:#fff;font-weight:500;font-size:16px;letter-spacing:.3px;border-right:1px solid #333}
.panel th:last-child{border-right:none}
.panel td{height:64px;text-align:center;font-family:"Roboto Condensed",sans-serif;font-size:16px;border-right:1px solid var(--line)}
.panel tr:nth-child(even) td{background:var(--row-alt)}
.stats table{width:332px}.stats td{width:166px}
.trades table{width:628px}
.scroll{position:absolute;right:0;top:65px;width:37px;height:388px;background:#c9c9c9}
.scroll .rail{position:absolute;left:10px;top:24px;width:18px;height:345px;border-radius:9px;background:linear-gradient(#666,#111 60%,#000)}
.scroll .thumb{position:absolute;left:10px;top:24px;width:18px;height:70px;border-radius:9px;background:linear-gradient(90deg,#aaa,#ddd,#999);border:1px solid #777}
</style>
</head>
<body>
<div class="app">
  <nav class="topnav">
    <div class="cell brand">PELLWORTH</div>
    <div class="cell w83">250D</div>
    <div class="cell w83">83D</div>
    <div class="cell w83">42D</div>
    <div class="cell gap"></div>
    <div class="cell models"><svg width="22" height="20" viewBox="0 0 22 20"><path d="M11 1 1 10h3v9h5v-6h4v6h5v-9h3z" fill="#111"/></svg>MODELS</div>
    <div class="cell sens"><svg width="22" height="22" viewBox="0 0 22 22"><g fill="none" stroke="#111" stroke-width="1.6"><circle cx="11" cy="11" r="3"/><circle cx="11" cy="11" r="7" stroke-dasharray="2 2"/><circle cx="11" cy="11" r="10" stroke-dasharray="1.5 2.5"/></g></svg>SENSITIVITIES</div>
    <div class="cell port"><svg width="22" height="22" viewBox="0 0 22 22"><g fill="none" stroke="#111" stroke-width="1.8"><circle cx="6" cy="6" r="4"/><circle cx="16" cy="6" r="4"/><circle cx="6" cy="16" r="4"/><circle cx="16" cy="16" r="4"/></g></svg>PORTFOLIO</div>
    <div class="cell backtest"><svg width="24" height="20" viewBox="0 0 24 20"><g fill="none" stroke="#fff" stroke-width="1.8"><rect x="1" y="1" width="22" height="18"/><path d="M4 15l5-6 4 4 6-8"/></g></svg>BACKTEST</div>
  </nav>

  <aside class="sidetab">
    <span>SELECT A MODEL</span>
    <svg class="toggle" width="26" height="26" viewBox="0 0 26 26"><circle cx="13" cy="13" r="12" fill="var(--navy)" stroke="#fff" stroke-width="2"/><path d="M18 13H8m4-4-4 4 4 4" stroke="#fff" stroke-width="2" fill="none"/></svg>
  </aside>

  <section class="chartcard">
    <div class="cardhead">
      <div class="tab chart">CHART</div>
      <div class="tab t1">#1</div>
      <div class="tab t2">#2</div>
      <div class="tab t3">#3</div>
      <div class="tab t4">#4</div>
    </div>
    <svg class="plot" width="1071" height="314" viewBox="105 200 1160 340" font-family="Open Sans, sans-serif" font-size="11" fill="#555">
      <g stroke="#eee" stroke-width="1">
        <path d="M190 263H1110M190 300H1110M190 337H1110M190 375H1110M190 412H1110"/>
        <path d="M217 255V450M360 255V450M500 255V450M640 255V450M777 255V450M917 255V450M1058 255V450"/>
      </g>
      <path d="M190 450H1110" stroke="#888" stroke-width="1.5"/>
      <g text-anchor="end"><text x="186" y="267">100</text><text x="186" y="304">80</text><text x="186" y="341">60</text><text x="186" y="379">40</text><text x="186" y="416">20</text><text x="186" y="454">0</text></g>
      <g text-anchor="middle"><text x="217" y="476">Jul 2018</text><text x="360" y="476">Sep 2018</text><text x="500" y="476">Nov 2018</text><text x="640" y="476">Jan 2019</text><text x="777" y="476">Mar 2019</text><text x="917" y="476">May 2019</text><text x="1058" y="476">Jul 2019</text></g>
      <g stroke-linecap="round" stroke-width="7" fill="none">
        <path d="M237 264H318M800 265H1040M860 268H990" stroke="var(--olive)" stroke-dasharray="0 5"/>
        <path d="M625 263H1060" stroke="var(--blue)" stroke-dasharray="0 5.5"/>
      </g>
      <g fill="var(--olive)">
        <circle cx="322" cy="270" r="3.5"/><circle cx="324" cy="276" r="3.5"/><circle cx="330" cy="268" r="3.5"/><circle cx="336" cy="264" r="3.5"/><circle cx="342" cy="268" r="3.5"/><circle cx="348" cy="266" r="3.5"/><circle cx="352" cy="270" r="3.5"/><circle cx="356" cy="268" r="3.5"/><circle cx="366" cy="270" r="3.5"/><circle cx="370" cy="274" r="3.5"/><circle cx="372" cy="328" r="3.5"/><circle cx="374" cy="360" r="3.5"/><circle cx="378" cy="380" r="3.5"/><circle cx="384" cy="340" r="3.5"/><circle cx="388" cy="345" r="3.5"/><circle cx="392" cy="365" r="3.5"/><circle cx="398" cy="375" r="3.5"/><circle cx="402" cy="360" r="3.5"/><circle cx="406" cy="355" r="3.5"/><circle cx="410" cy="370" r="3.5"/><circle cx="415" cy="322" r="3.5"/><circle cx="418" cy="330" r="3.5"/><circle cx="422" cy="303" r="3.5"/><circle cx="428" cy="292" r="3.5"/><circle cx="433" cy="290" r="3.5"/><circle cx="436" cy="265" r="3.5"/><circle cx="441" cy="268" r="3.5"/><circle cx="444" cy="338" r="3.5"/><circle cx="448" cy="325" r="3.5"/><circle cx="452" cy="350" r="3.5"/><circle cx="458" cy="355" r="3.5"/><circle cx="462" cy="345" r="3.5"/><circle cx="466" cy="400" r="3.5"/><circle cx="470" cy="415" r="3.5"/><circle cx="475" cy="420" r="3.5"/><circle cx="480" cy="410" r="3.5"/><circle cx="484" cy="398" r="3.5"/><circle cx="488" cy="415" r="3.5"/><circle cx="492" cy="428" r="3.5"/><circle cx="496" cy="412" r="3.5"/><circle cx="500" cy="432" r="3.5"/><circle cx="504" cy="442" r="3.5"/><circle cx="508" cy="435" r="3.5"/><circle cx="512" cy="440" r="3.5"/><circle cx="516" cy="430" r="3.5"/><circle cx="520" cy="432" r="3.5"/><circle cx="524" cy="398" r="3.5"/><circle cx="530" cy="420" r="3.5"/><circle cx="534" cy="405" r="3.5"/><circle cx="538" cy="400" r="3.5"/><circle cx="543" cy="385" r="3.5"/><circle cx="548" cy="388" r="3.5"/><circle cx="552" cy="395" r="3.5"/><circle cx="556" cy="392" r="3.5"/><circle cx="560" cy="410" r="3.5"/><circle cx="563" cy="348" r="3.5"/><circle cx="566" cy="337" r="3.5"/><circle cx="570" cy="340" r="3.5"/><circle cx="575" cy="265" r="3.5"/><circle cx="580" cy="268" r="3.5"/><circle cx="585" cy="263" r="3.5"/><circle cx="592" cy="265" r="3.5"/><circle cx="598" cy="268" r="3.5"/><circle cx="604" cy="276" r="3.5"/><circle cx="608" cy="284" r="3.5"/><circle cx="612" cy="436" r="3.5"/><circle cx="616" cy="440" r="3.5"/><circle cx="626" cy="436" r="3.5"/><circle cx="630" cy="432" r="3.5"/><circle cx="636" cy="440" r="3.5"/><circle cx="642" cy="430" r="3.5"/><circle cx="646" cy="425" r="3.5"/><circle cx="652" cy="430" r="3.5"/><circle cx="656" cy="436" r="3.5"/><circle cx="660" cy="428" r="3.5"/><circle cx="664" cy="433" r="3.5"/><circle cx="672" cy="440" r="3.5"/><circle cx="676" cy="430" r="3.5"/><circle cx="680" cy="408" r="3.5"/><circle cx="684" cy="400" r="3.5"/><circle cx="688" cy="398" r="3.5"/><circle cx="692" cy="398" r="3.5"/><circle cx="688" cy="326" r="3.5"/><circle cx="703" cy="327" r="3.5"/><circle cx="694" cy="365" r="3.5"/><circle cx="697" cy="378" r="3.5"/><circle cx="706" cy="292" r="3.5"/><circle cx="708" cy="284" r="3.5"/><circle cx="724" cy="286" r="3.5"/><circle cx="726" cy="340" r="3.5"/><circle cx="728" cy="405" r="3.5"/><circle cx="734" cy="408" r="3.5"/><circle cx="738" cy="420" r="3.5"/><circle cx="740" cy="285" r="3.5"/><circle cx="744" cy="298" r="3.5"/><circle cx="748" cy="310" r="3.5"/><circle cx="742" cy="320" r="3.5"/><circle cx="754" cy="320" r="3.5"/><circle cx="756" cy="363" r="3.5"/><circle cx="758" cy="273" r="3.5"/><circle cx="766" cy="285" r="3.5"/><circle cx="770" cy="280" r="3.5"/><circle cx="774" cy="278" r="3.5"/><circle cx="780" cy="268" r="3.5"/><circle cx="786" cy="272" r="3.5"/><circle cx="790" cy="278" r="3.5"/><circle cx="795" cy="265" r="3.5"/>
      </g>
      <g fill="var(--blue)">
        <circle cx="237" cy="328" r="3.5"/><circle cx="240" cy="275" r="3.5"/><circle cx="243" cy="268" r="3.5"/><circle cx="246" cy="268" r="3.5"/><circle cx="250" cy="272" r="3.5"/><circle cx="256" cy="273" r="3.5"/><circle cx="258" cy="344" r="3.5"/><circle cx="260" cy="378" r="3.5"/><circle cx="266" cy="372" r="3.5"/><circle cx="270" cy="388" r="3.5"/><circle cx="273" cy="405" r="3.5"/><circle cx="276" cy="395" r="3.5"/><circle cx="280" cy="382" r="3.5"/><circle cx="284" cy="378" r="3.5"/><circle cx="288" cy="380" r="3.5"/><circle cx="288" cy="397" r="3.5"/><circle cx="290" cy="340" r="3.5"/><circle cx="294" cy="364" r="3.5"/><circle cx="298" cy="368" r="3.5"/><circle cx="302" cy="365" r="3.5"/><circle cx="306" cy="365" r="3.5"/><circle cx="304" cy="342" r="3.5"/><circle cx="308" cy="405" r="3.5"/><circle cx="314" cy="395" r="3.5"/><circle cx="318" cy="398" r="3.5"/><circle cx="322" cy="382" r="3.5"/><circle cx="326" cy="378" r="3.5"/><circle cx="330" cy="375" r="3.5"/><circle cx="332" cy="398" r="3.5"/><circle cx="336" cy="392" r="3.5"/><circle cx="340" cy="400" r="3.5"/><circle cx="344" cy="404" r="3.5"/><circle cx="348" cy="392" r="3.5"/><circle cx="352" cy="402" r="3.5"/><circle cx="356" cy="398" r="3.5"/><circle cx="366" cy="408" r="3.5"/><circle cx="370" cy="412" r="3.5"/><circle cx="372" cy="428" r="3.5"/><circle cx="376" cy="432" r="3.5"/><circle cx="380" cy="432" r="3.5"/><circle cx="384" cy="428" r="3.5"/><circle cx="388" cy="422" r="3.5"/><circle cx="390" cy="428" r="3.5"/><circle cx="394" cy="430" r="3.5"/><circle cx="398" cy="425" r="3.5"/><circle cx="402" cy="420" r="3.5"/><circle cx="404" cy="432" r="3.5"/><circle cx="408" cy="425" r="3.5"/><circle cx="412" cy="425" r="3.5"/><circle cx="416" cy="408" r="3.5"/><circle cx="420" cy="400" r="3.5"/><circle cx="424" cy="395" r="3.5"/><circle cx="428" cy="392" r="3.5"/><circle cx="432" cy="398" r="3.5"/><circle cx="436" cy="412" r="3.5"/><circle cx="440" cy="400" r="3.5"/><circle cx="444" cy="412" r="3.5"/><circle cx="448" cy="408" r="3.5"/><circle cx="452" cy="392" r="3.5"/><circle cx="456" cy="412" r="3.5"/><circle cx="460" cy="410" r="3.5"/><circle cx="462" cy="398" r="3.5"/><circle cx="466" cy="445" r="3.5"/><circle cx="470" cy="446" r="3.5"/><circle cx="476" cy="432" r="3.5"/><circle cx="480" cy="442" r="3.5"/><circle cx="486" cy="430" r="3.5"/><circle cx="492" cy="412" r="3.5"/><circle cx="496" cy="392" r="3.5"/><circle cx="498" cy="320" r="3.5"/><circle cx="502" cy="292" r="3.5"/><circle cx="508" cy="288" r="3.5"/><circle cx="512" cy="300" r="3.5"/><circle cx="514" cy="276" r="3.5"/><circle cx="516" cy="284" r="3.5"/><circle cx="520" cy="300" r="3.5"/><circle cx="526" cy="298" r="3.5"/><circle cx="528" cy="420" r="3.5"/><circle cx="532" cy="425" r="3.5"/><circle cx="536" cy="412" r="3.5"/><circle cx="540" cy="410" r="3.5"/><circle cx="544" cy="402" r="3.5"/><circle cx="548" cy="402" r="3.5"/><circle cx="556" cy="410" r="3.5"/><circle cx="560" cy="408" r="3.5"/><circle cx="564" cy="385" r="3.5"/><circle cx="568" cy="368" r="3.5"/><circle cx="572" cy="370" r="3.5"/><circle cx="576" cy="285" r="3.5"/><circle cx="580" cy="280" r="3.5"/><circle cx="584" cy="272" r="3.5"/><circle cx="588" cy="265" r="3.5"/><circle cx="592" cy="263" r="3.5"/><circle cx="596" cy="272" r="3.5"/><circle cx="600" cy="275" r="3.5"/><circle cx="606" cy="270" r="3.5"/><circle cx="612" cy="265" r="3.5"/><circle cx="616" cy="263" r="3.5"/><circle cx="620" cy="263" r="3.5"/>
      </g>
      <g fill="var(--green)"><circle cx="1035" cy="447" r="3.5"/><circle cx="1040" cy="447" r="3.5"/><circle cx="1045" cy="447" r="3.5"/></g>
      <text x="1167" y="265" font-family="Times New Roman, serif" font-size="12" fill="#444">Names</text>
      <g>
        <circle cx="1150" cy="261" r="3.5" fill="#9ab8d8"/><circle cx="1150" cy="280" r="3.5" fill="#f5b27a"/><circle cx="1150" cy="298" r="3.5" fill="#4c9a2a"/><circle cx="1150" cy="317" r="3.5" fill="#e08c92"/><circle cx="1150" cy="336" r="3.5" fill="#c8a8d8"/><circle cx="1150" cy="354" r="3.5" fill="#c8a898"/><circle cx="1150" cy="373" r="3.5" fill="#f0b8d8"/><circle cx="1150" cy="392" r="3.5" fill="#bbb"/><circle cx="1150" cy="410" r="3.5" fill="var(--olive)"/><circle cx="1150" cy="429" r="3.5" fill="#8ad8e0"/><circle cx="1150" cy="447" r="3.5" fill="var(--blue)"/>
      </g>
    </svg>
  </section>

  <div class="export" style="left:383px"><svg width="24" height="22" viewBox="0 0 24 22"><g fill="none" stroke="var(--navy)" stroke-width="2"><path d="M10 4H2v16h16v-7"/><path d="M7 15c1-6 5-9 12-9M15 2l5 4-5 4"/></g></svg>Export</div>
  <div class="export" style="left:1085px"><svg width="24" height="22" viewBox="0 0 24 22"><g fill="none" stroke="var(--navy)" stroke-width="2"><path d="M10 4H2v16h16v-7"/><path d="M7 15c1-6 5-9 12-9M15 2l5 4-5 4"/></g></svg>Export</div>

  <section class="panel stats">
    <table>
      <tr><th colspan="2">Stats</th></tr>
      <tr><td>Stat 1</td><td>0.5</td></tr>
      <tr><td>Stat 2</td><td>-3</td></tr>
      <tr><td>Stat 3</td><td>30%</td></tr>
      <tr><td>Stat 4</td><td>0.5</td></tr>
      <tr><td>Stat 5</td><td>-3</td></tr>
      <tr><td>Stat 6</td><td>30%</td></tr>
    </table>
    <div class="scroll"><div class="rail"></div><div class="thumb"></div></div>
  </section>

  <section class="panel trades">
    <table>
      <tr><th>Open</th><th>Close</th><th>Size</th><th>Return</th></tr>
      <tr><td>2018-04-05</td><td>2018-04-07</td><td>13</td><td>5%</td></tr>
      <tr><td>2018-04-05</td><td>2018-04-07</td><td>12</td><td>7%</td></tr>
      <tr><td>2018-04-05</td><td>2018-04-07</td><td>15</td><td>6%</td></tr>
      <tr><td>2018-04-05</td><td>2018-04-07</td><td>16</td><td>9%</td></tr>
      <tr><td>2018-04-05</td><td>2018-04-07</td><td>12</td><td>8%</td></tr>
      <tr><td>2018-04-05</td><td>2018-04-07</td><td>19</td><td>6%</td></tr>
    </table>
    <div class="scroll"><div class="rail"></div><div class="thumb"></div></div>
  </section>
</div>
</body>
</html>
```